Visitenkarten-Design für virtuelle Jobmesse & Jobbörse für Soldaten
Zielgruppe
Die KVL GmbH ist ein Unternehmen das zwei Hauptprodukte betreibt! Zum einen Jobbörse für Soldaten unter www.laufbahnwechsel-beispiel.de und zum anderen eine virtuelle Jobmesse für Soldaten unter www.merivon-beispiel.de , die wir zweimal im Jahr veranstalten.
Aufgabenstellung
Wir haben ja die beiden Produkte Laufbahnwechsel.de und die Merivon, für die bereits jeweils ein separtes Logo besteht! Diese finden Sie im Anhang! Beide werden doch jedoch von einem Unternehmen, der KVL GmbH betrieben! Aktuell nutzen wir eine Visitenkarte mit dem Logo von KVL und eine mit dem Logo der MERIVON. Gerade im Hinblick darauf, dass wir zukünftig auch weiter Plattformen in unser Portfolio aufnehmen, möchte ich hier unsere V-Karten flexibler gestalten!
Ziel soll es also sein, eine Visitenkarte zu gestalten, auf dem klar wird, dass der Mitarbeiter von der KVL GmbH kommt, die KVL GmbH aber unterschiedliche Produkte betreibt.
Im Anhang finden Sie:
1. Das Logo von KVL
2. Das Logo von Merivon
3. Die aktuelle V-Karte von KVL
4. Die aktuelle V-Karte von MERIVON
Vielleicht ein kleiner Anreiz: Aktuell nutzen wir auch zwei getrennte Geschäftspapiere. Das von www.laufbahnwechsel-beispiel.de lade ich einmal hoch! Der Designer, der auch die Visitenkarte erstellt, erhällt im Anschluss den 1:1 Auftrag in Höhe von 200 Euro für die Erstellung des Geschäftspapiers! Wenn Sie jetzt schon einen Vorschlag für das Geschäftspapier einreichen, erhöht das natürlich Ihre Chancen, wobei ich verspreche, dass wir im Falle eine Annahme das 1:1 im Anschluß dennoch starten werden!

```html
<!DOCTYPE html>
<html lang="de">
<head>
<meta charset="utf-8">
<title>Visitenkarte KVL GmbH</title>
<link rel="stylesheet" href="https://fonts.googleapis.com/css2?family=Arimo:wght@400;700&display=swap">
<style>
  :root{
    --bg:#1b1b1b;
    --card:#262626;
    --blue:#2f4f95;
    --grey-line:#8c8c8c;
    --silver:#c9c9c9;
    --text-grey:#5e5e5e;
    --green:#4a6a2c;
    --green-band:#465e2b;
    --white:#f2f2f2;
  }
  *{margin:0;padding:0;box-sizing:border-box}
  html,body{width:1200px;height:801px;overflow:hidden;background:var(--bg);font-family:"Arimo",Arial,sans-serif}
  .card{position:absolute;top:238px;width:520px;height:325px;background:var(--card);overflow:hidden;box-shadow:0 10px 30px rgba(0,0,0,.5)}
  .card--front{left:50px}
  .card--back{left:630px}
  .stripes{position:absolute;left:0;top:0}
  .brand-name{position:absolute;color:var(--silver);font-weight:400;letter-spacing:1px}
  .front-brand{left:28px;top:78px;font-size:24px}
  .front-company{position:absolute;left:30px;top:118px;font-size:22px;color:var(--text-grey)}
  .person-name{position:absolute;left:260px;top:22px;font-size:24px;color:var(--blue)}
  .person-role{position:absolute;left:262px;top:52px;font-size:13px;color:var(--text-grey)}
  .address{position:absolute;left:262px;top:100px;font-size:13px;line-height:19px;color:var(--text-grey)}
  .contact{position:absolute;left:262px;top:175px;font-size:12px;line-height:19px;color:var(--text-grey)}
  .contact .label{color:var(--blue);display:inline-block;width:58px}
  .contact .label--green{color:var(--green)}
  .product-mark{position:absolute;left:40px;top:200px;display:flex;align-items:center;gap:8px}
  .product-mark .dot{width:10px;height:10px;border-radius:50%;background:var(--green)}
  .product-mark .name{font-size:20px;color:var(--green);letter-spacing:1px}
  .product-url{position:absolute;left:40px;top:236px;font-size:16px;font-weight:700;color:var(--green)}
  .product-note{position:absolute;left:40px;top:262px;font-size:11px;color:var(--text-grey)}
  .back-brand{left:0;right:0;top:72px;text-align:center;font-size:30px}
  .back-product{position:absolute;left:0;right:0;top:132px;display:flex;justify-content:center;align-items:center;gap:10px}
  .back-product .dot{width:12px;height:12px;border-radius:50%;background:var(--green)}
  .back-product .name{font-size:26px;color:var(--green);letter-spacing:2px}
  .band{position:absolute;height:36px;display:flex;align-items:center;color:var(--white);font-weight:700;font-size:15px}
  .band--green{left:0;bottom:0;width:250px;background:var(--green-band);padding-left:14px}
  .band--blue{right:0;bottom:0;width:250px;background:var(--blue);justify-content:flex-end;padding-right:12px;font-size:13px}
  .bars{position:absolute;left:254px;bottom:0;display:flex;gap:4px}
  .bars span{width:4px;height:36px;background:#9a9a9a}
</style>
</head>
<body>
  <section class="card card--front" aria-label="Visitenkarte Vorderseite">
    <svg class="stripes" width="520" height="325" aria-hidden="true">
      <line x1="0" y1="70" x2="520" y2="70" stroke="var(--blue)" stroke-width="3"/>
      <line x1="0" y1="76" x2="520" y2="76" stroke="var(--grey-line)" stroke-width="2"/>
    </svg>
    <div class="brand-name front-brand">Laufbahnwechsel</div>
    <div class="front-company">KVL GmbH</div>
    <div class="person-name">Jonas Berger</div>
    <div class="person-role">Geschäftsführer</div>
    <div class="address">Lindenweg 14<br>86000 Musterstadt</div>
    <div class="contact">
      <div><span class="label">Telefon:</span>0800 - 123 45 67</div>
      <div><span class="label">Mobil:</span>0170 - 000 12 345</div>
      <div><span class="label label--green">E:</span>j.berger@laufbahnwechsel-beispiel.de</div>
      <div><span class="label label--green">E:</span>j.berger@merivon-beispiel.de</div>
    </div>
    <div class="product-mark"><span class="dot"></span><span class="name">MERIVON</span></div>
    <div class="product-url">Merivon.de</div>
    <div class="product-note">ist eine Marke der KVL GmbH</div>
  </section>

  <section class="card card--back" aria-label="Visitenkarte Rückseite">
    <svg class="stripes" width="520" height="325" aria-hidden="true">
      <line x1="0" y1="100" x2="520" y2="22" stroke="var(--blue)" stroke-width="3"/>
      <line x1="0" y1="108" x2="520" y2="30" stroke="var(--grey-line)" stroke-width="2"/>
    </svg>
    <div class="brand-name back-brand">Laufbahnwechsel</div>
    <div class="back-product"><span class="dot"></span><span class="name">MERIVON</span></div>
    <div class="band band--green">www.merivon-beispiel.de</div>
    <div class="bars" aria-hidden="true"><span></span><span></span><span></span></div>
    <div class="band band--blue">www.laufbahnwechsel-beispiel.de</div>
  </section>
</body>
</html>
```